Harborline Auto LLC

Car Dealer Customer Service
Address: 2874 Cresthaven Road, Alderbrook, QX 00162
web: www.harborlineautoxq.net
email: harborlineautoxq@mailnest.example
Phone: (555) 555-0148
Phone: (555) 555-0173

```html
<!DOCTYPE html>
<html lang="en">
<head>
<meta charset="utf-8">
<title>Harborline Auto – Business Card</title>
<link rel="stylesheet" href="https://fonts.googleapis.com/css2?family=Poppins:ital,wght@0,400;0,600;0,700;1,400&display=swap">
<style>
  :root{
    --backdrop:#2b2b2b;
    --card-dark:#1b1c1e;
    --card-light:#f4f4f2;
    --brand-blue:#1f7ab3;
    --brand-gold:#e2a83a;
    --ink:#1d1d1d;
    --pattern-a:#151516;
    --pattern-b:#4a4a4c;
  }
  *{margin:0;padding:0;box-sizing:border-box}
  html,body{width:1200px;height:1138px;overflow:hidden;background:var(--backdrop);font-family:"Poppins",sans-serif}
  .card{position:absolute;border-radius:16px;overflow:hidden}
  .card--front{left:274px;top:185px;width:623px;height:377px;background:var(--card-dark)}
  .front-pattern{position:absolute;left:95px;top:0;right:0;bottom:0;
    background:linear-gradient(90deg,var(--pattern-a) 0%,#2c2c2e 45%,var(--pattern-b) 100%)}
  .front-name{position:absolute;left:28px;top:35px;writing-mode:vertical-rl;
    font-weight:700;font-size:30px;letter-spacing:1px;color:var(--brand-blue);line-height:1}
  .front-mark{position:absolute;left:100px;top:122px;width:92px;height:92px;border-radius:50%;background:var(--brand-gold)}

  .card--back{left:276px;top:608px;width:618px;height:374px;background:var(--card-light)}
  .back-frame{position:absolute;width:374px;height:618px;left:122px;top:-122px;transform:rotate(90deg);transform-origin:center}
  .back-mark{position:absolute;left:118px;top:62px;width:140px;height:140px;border-radius:50%;background:var(--brand-blue)}
  .back-name{position:absolute;left:0;right:0;text-align:center;top:218px;font-weight:700;font-size:28px;letter-spacing:.5px;color:var(--brand-blue);line-height:1;white-space:nowrap}
  .tagline{position:absolute;left:42px;top:293px;font-style:italic;font-size:17px;color:var(--ink);white-space:nowrap}
  .phones{position:absolute;left:76px;top:325px;list-style:none}
  .phones li{display:flex;align-items:center;gap:12px;font-weight:700;font-size:22px;color:var(--brand-blue);line-height:27px;white-space:nowrap}
  .phones svg{width:16px;height:16px;flex:none}
  .divider{position:absolute;left:66px;width:244px;top:438px;display:flex;align-items:center;gap:8px}
  .divider .rule{flex:1;height:1.5px;background:var(--brand-blue)}
  .divider svg{width:15px;height:15px}
  .contact{position:absolute;left:0;right:0;top:467px;text-align:center;font-size:14.5px;font-style:normal;color:var(--ink);line-height:22px;white-space:nowrap}
  .contact .accent{color:var(--brand-gold)}
</style>
</head>
<body>
  <section class="card card--front">
    <div class="front-pattern" role="img" aria-label="Embossed repeating brand pattern in black and grey"></div>
    <h1 class="front-name">HARBORLINE AUTO</h1>
    <div class="front-mark"></div>
  </section>

  <section class="card card--back">
    <div class="back-frame">
      <div class="back-mark"></div>
      <h2 class="back-name">HARBORLINE AUTO</h2>
      <p class="tagline">Car Dealer Customer Service</p>
      <ul class="phones">
        <li><svg viewBox="0 0 16 16"><path fill="#e2a83a" d="M2 6c0-2 2-3 6-3s6 1 6 3v1h-3V5.5H5V7H2zM4 8h8l1.5 6h-11z"/></svg>(555) 555-0148</li>
        <li><svg viewBox="0 0 16 16"><path fill="#e2a83a" d="M2 6c0-2 2-3 6-3s6 1 6 3v1h-3V5.5H5V7H2zM4 8h8l1.5 6h-11z"/></svg>(555) 555-0173</li>
      </ul>
      <div class="divider">
        <span class="rule"></span>
        <svg viewBox="0 0 16 16"><circle cx="8" cy="8" r="6.5" fill="none" stroke="#e2a83a" stroke-width="1.4"/><path d="M1.5 8h13M8 1.5c-3 3-3 10 0 13M8 1.5c3 3 3 10 0 13" fill="none" stroke="#e2a83a" stroke-width="1.2"/></svg>
        <svg viewBox="0 0 16 16"><rect x="1.5" y="3.5" width="13" height="9" fill="none" stroke="#e2a83a" stroke-width="1.4"/><path d="M1.5 3.5l6.5 5 6.5-5" fill="none" stroke="#e2a83a" stroke-width="1.4"/></svg>
        <svg viewBox="0 0 16 16"><circle cx="8" cy="8" r="6.5" fill="none" stroke="#e2a83a" stroke-width="1.4"/><path d="M8 4a2.5 2.5 0 0 0-2.5 2.5C5.5 9 8 12 8 12s2.5-3 2.5-5.5A2.5 2.5 0 0 0 8 4z" fill="#e2a83a"/></svg>
        <span class="rule"></span>
      </div>
      <address class="contact">
        harborlineautoxq@mailnest.example<br>
        www.<span class="accent">harborline</span>autoxq.net<br>
        2874 Cresthaven Road,<br>
        Alderbrook, QX 00162
      </address>
    </div>
  </section>
</body>
</html>
```